Stationery Design Project for Nimbora, Chicago

Nimbora, a street parking application which helps car drivers find a street parking spot by offering an ideal path along which to look for parking. This path is calculated by our algorithm based on data (e.g. historical data, baseball games schedule, etc.). Along this path the driver will find a spot and will also save 70% of the search time. Customer we target is reg. between 21 and 45 yo.

We envision something young, fresh, bright and original. Slightly abstract maybe. It should represent the idea and elements of finding street parking in the city, e.g. car(s), parking spot, people, city, etc. (just ideas!).

Logo is attached.

Requirement:
- Business Cards (2 Sided Full Color CMYK)
- Letterhead (1 Sided Full Color CMYK)
- Envelope (1 Sided Full Color CMYK)
- Sticker (1 Sided Full Color CMYK), round with a 2inch diameter.

Reason: We're starting to get more and more designs and need more time to look into all of them. Very exciting!! Thanks to everybody!

Hi all, we're in the process of selecting our favs. Though choices!!! Really good submissions. Will keep you posted and sorry for the delay.

Target Market(s)

Car drivers and owners between 21 and 45

Industry/Entity Type

Parking

Requirements
Must have
• Sticker should be round and include company URL nimbora.com and the new logo which we will attach soon.
Should not have
• Should not be too serious or boring.

```html
<!DOCTYPE html>
<html lang="en">
<head>
<meta charset="utf-8">
<title>Nimbora Business Card</title>
<link rel="stylesheet" href="https://fonts.googleapis.com/css2?family=Source+Sans+3:wght@400;600;700&display=swap">
<style>
  :root {
    --backdrop: #e6e7e9;
    --card: #ffffff;
    --accent-cyan: #0aa3de;
    --brand-navy: #1d3a8f;
    --mark-blue: #1a5cc4;
    --wordmark: #1c1d20;
    --body-text: #4a4a4a;
  }
  * { box-sizing: border-box; margin: 0; padding: 0; }
  html, body {
    width: 954px;
    height: 1200px;
    overflow: hidden;
    background: var(--backdrop);
    font-family: "Source Sans 3", Arial, sans-serif;
  }
  .card {
    position: absolute;
    left: 78px;
    width: 797px;
    height: 453px;
    background: var(--card);
    border-radius: 30px;
    overflow: hidden;
  }
  .card--front { top: 110px; }
  .card--back { top: 642px; }

  .edge-tab {
    position: absolute;
    top: 66px;
    width: 14px;
    height: 202px;
    background: var(--accent-cyan);
  }
  .edge-tab--left { left: 0; border-radius: 0 4px 4px 0; }
  .edge-tab--right { right: 0; border-radius: 4px 0 0 4px; }

  .brand {
    position: absolute;
    display: flex;
    align-items: center;
  }
  .brand__dot {
    border-radius: 50%;
    background: var(--mark-blue);
    flex: none;
  }
  .brand__name {
    color: var(--wordmark);
    font-weight: 700;
    line-height: 1;
    letter-spacing: 0.5px;
  }
  .card--front .brand { left: 131px; top: 98px; gap: 42px; }
  .card--front .brand__dot { width: 124px; height: 124px; }
  .card--front .brand__name { font-size: 92px; }

  .card--back .brand { left: 112px; top: 133px; gap: 34px; }
  .card--back .brand__dot { width: 160px; height: 160px; }
  .card--back .brand__name { font-size: 104px; }

  .contact {
    position: absolute;
    left: 0;
    right: 0;
    top: 290px;
    text-align: center;
    color: var(--body-text);
    font-size: 22px;
    line-height: 32px;
  }
  .contact__person {
    font-size: 27px;
    font-weight: 700;
    color: var(--brand-navy);
    line-height: 34px;
    margin-bottom: 10px;
  }
  .contact__role {
    font-size: 22px;
    color: var(--accent-cyan);
  }
  .contact__label { font-weight: 700; }
</style>
</head>
<body>
  <section class="card card--front">
    <div class="edge-tab edge-tab--left"></div>
    <div class="edge-tab edge-tab--right"></div>
    <div class="brand">
      <span class="brand__dot"></span>
      <span class="brand__name">Nimbora</span>
    </div>
    <div class="contact">
      <p class="contact__person">Your Name - <span class="contact__role">Designation</span></p>
      <p><span class="contact__label">p</span> : 123-456-7890 &nbsp;|&nbsp; <span class="contact__label">c</span> : 123-456-7890</p>
      <p><span class="contact__label">e</span> : name@website.com &nbsp;|&nbsp; <span class="contact__label">w</span> : www.website.com</p>
      <p>City Name, Street Name, State Name, Country Code</p>
    </div>
  </section>

  <section class="card card--back">
    <div class="brand">
      <span class="brand__dot"></span>
      <span class="brand__name">Nimbora</span>
    </div>
  </section>
</body>
</html>
```